Bluecrest Learning Corps by graduating students from college in two years

Based on the logo design, create stationary and business cards for
Dr. Venrel T Oskamp, CEO, (703) 482-1736
and Marisa Deltoft, Respresentative, (301) 647-2208
Address: 4719 Pellham Court, Ashbrook Landing, VA 22187
Incorporate elelments of the logo

Target Market(s)

USA

Font styles to use
Other font styles liked:
• match with the logo type style

```html
<!DOCTYPE html>
<html lang="en">
<head>
<meta charset="utf-8">
<title>Bluecrest Learning Corps — Letterhead</title>
<link rel="stylesheet" href="https://fonts.googleapis.com/css2?family=Arimo:wght@400;700&display=swap">
<style>
  :root {
    --navy: #0b2161;
    --gold: #f4c22f;
    --paper: #ffffff;
    --backdrop: #d9dadc;
    --ink: #4a4a4a;
    --ink-dark: #3a3a3a;
    --ghost: #eef0f4;
  }
  * { margin: 0; padding: 0; box-sizing: border-box; }
  html, body {
    width: 1200px; height: 1159px; overflow: hidden;
    background: var(--backdrop);
    font-family: "Arimo", Arial, sans-serif;
  }
  .letterhead {
    position: absolute; left: 175px; top: 30px;
    width: 850px; height: 1100px;
    background: var(--paper);
    overflow: hidden;
    box-shadow: 0 6px 24px rgba(0,0,0,.18);
  }
  .header-band {
    position: absolute; left: 0; top: 140px;
    width: 100%; height: 78px;
    background: var(--navy);
    border-top: 3px solid var(--gold);
    border-bottom: 3px solid var(--gold);
  }
  .brand-seal {
    position: absolute; left: 38px; top: 104px;
    width: 150px; height: 150px; border-radius: 50%;
    background: var(--paper);
    border: 6px solid var(--gold);
    box-shadow: 0 0 0 5px var(--navy);
    display: flex; align-items: center; justify-content: center;
    text-align: center; padding: 18px;
  }
  .brand-name {
    color: var(--navy); font-weight: 700; font-size: 17px; line-height: 1.2;
  }
  .contact-row {
    position: absolute; left: 230px; top: 146px; height: 66px;
    display: flex; align-items: center;
  }
  .contact {
    color: #fff; font-size: 14px; line-height: 1.25; padding: 0 34px;
  }
  .contact:first-child { padding-left: 0; }
  .contact + .contact { border-left: 1px solid var(--gold); }
  .contact-name { color: var(--gold); font-weight: 700; font-size: 16px; }
  .contact-phone { display: flex; align-items: center; gap: 5px; }
  .contact-phone svg { width: 11px; height: 11px; fill: #fff; }

  .letter-body {
    position: absolute; left: 185px; top: 390px; width: 580px;
    color: var(--ink); font-size: 13.5px; line-height: 1.3;
  }
  .salutation { font-weight: 700; font-size: 18px; color: var(--ink-dark); margin-bottom: 26px; }
  .letter-body p { margin-bottom: 22px; }
  .closing { font-weight: 700; font-size: 12px; color: var(--ink-dark); margin-top: 40px; }
  .signature-area {
    margin-top: 22px; width: 150px; height: 46px;
    background: linear-gradient(90deg, #f2f2f2, #fafafa);
    border-radius: 4px;
  }
  .backdrop-motif {
    position: absolute; right: -30px; bottom: -20px;
    width: 470px; height: 400px;
    background: radial-gradient(ellipse at 55% 45%, var(--ghost) 0%, rgba(238,240,244,0) 70%);
  }
</style>
</head>
<body>
  <main class="letterhead">
    <div class="header-band"></div>

    <div class="brand-seal">
      <span class="brand-name">Bluecrest Learning Corps</span>
    </div>

    <div class="contact-row">
      <div class="contact">
        <div class="contact-name">Dr. Venrel T Oskamp</div>
        <div class="contact-title">CEO</div>
        <div class="contact-phone">
          <svg viewBox="0 0 24 24" aria-hidden="true"><path d="M6.6 10.8a15 15 0 0 0 6.6 6.6l2.2-2.2a1 1 0 0 1 1-.25 11.4 11.4 0 0 0 3.6.57 1 1 0 0 1 1 1V20a1 1 0 0 1-1 1A17 17 0 0 1 3 4a1 1 0 0 1 1-1h3.5a1 1 0 0 1 1 1c0 1.250.2 2.450.57 3.6a1 1 0 0 1-.25 1z"/></svg>
          (703) 482-1736
        </div>
      </div>
      <div class="contact">
        <div class="contact-name">Marisa Deltoft</div>
        <div class="contact-title">Respresentative</div>
        <div class="contact-phone">
          <svg viewBox="0 0 24 24" aria-hidden="true"><path d="M6.6 10.8a15 15 0 0 0 6.6 6.6l2.2-2.2a1 1 0 0 1 1-.25 11.4 11.4 0 0 0 3.6.57 1 1 0 0 1 1 1V20a1 1 0 0 1-1 1A17 17 0 0 1 3 4a1 1 0 0 1 1-1h3.5a1 1 0 0 1 1 1c0 1.250.2 2.450.57 3.6a1 1 0 0 1-.25 1z"/></svg>
          (301) 647-2208
        </div>
      </div>
      <div class="contact contact-address">
        4719 Pellham Court<br>Ashbrook Landing<br>VA 22187
      </div>
    </div>

    <div class="backdrop-motif" role="img" aria-label="Faint decorative motif in the lower corner"></div>

    <section class="letter-body">
      <h1 class="salutation">Dear Mr. Halvorsen,</h1>
      <p>Lorem ipsum dolor sit amet, consectetuer adipiscing elit, sed diam nonmmy nibh euismod tincidunt ut laor eet dolore magna aliquam erat volutpat. Ut wisi enim ad minim veniam, quis nostrud exerci tationmcorper suscipit lobortis nisl ut aliquip ex ea commodo consequat. Duis autem vel eum iriure dolor in hendrerit in vulputate velit esse molestie consequat, vel illum dolore eu feugiat</p>
      <p>Rorem ipsum dolor sit amet, consectetuer adipiscing elit, sed diam nonmmy nibh euismod tincidunt ut laor eet dolore magna aliquam erat volutpat. Ut wisi enim ad minim veniam, quis nostrud exerci tationmcorper suscipit lobortis nisl ut aliquip ex ea commodo consequat. Duis autem vel eum iriure dolor in hendrerit in vulputate velit esse molest</p>
      <p>Dorem ipsum dolor sit amet, consectetuer adipiscing elit, sed diam nonmmy nibh euismod tincidunt ut laor eet dolore magna aliquam erat volutpat. Ut wisi enim ad minim veniam, quis nostrud exerci tationmcorper suscipit lobortis nisl ut aliquip ex ea commodo consequat. Duis autem vel eum iriure dolor in hendrerit in suscipit lobortis nisl ut aliquip ex ea commodo consequat. Duis autem vel eum iriure dolor in hendrerit in vulputate velit esse molestie consequat, vel illum</p>
      <p>Sorem ipsum dolor sit amet, consectetuer adipiscing elit, sed diam nonmmy nibh euismod tincidunt ut laor eet dolore magna aliquam erat volutpat. Ut wisi enim ad minim veniam, quis nostrud exerci tationmcorper suscipit lobortis nisl ut aliquip ex ea commodo consequat. Duis autem vel eum iriure dolor in</p>
      <div class="closing">Sincerely,</div>
      <div class="signature-area" role="img" aria-label="Handwritten signature"></div>
    </section>
  </main>
</body>
</html>
```